VELK Redesign

Make a more modern looking Homepage. Our page: www.velk-example.at
Should look like:
www.tarnok-example.com/at/de/
https://web.dovrand-example.com
https://id.pallomere-example.com

Target Market(s)

furniture industry

Number of Pages Required

1 page

Font styles to use
Sans Serif

Colors
3176b5

```html
<!DOCTYPE html>
<html lang="en">
<head>
<meta charset="utf-8">
<title>VELK – Decorative Furniture Fittings</title>
<link href="https://fonts.googleapis.com/css2?family=Lato:wght@400;700;900&display=swap" rel="stylesheet">
<style>
:root{
  --brand:#3176b5;
  --brand-dark:#245e94;
  --ink:#2f2f33;
  --muted:#7b7d82;
  --grey-band:#ececed;
  --footer-bg:#efeff0;
  --white:#ffffff;
  --line:#d9d9dc;
}
*{margin:0;padding:0;box-sizing:border-box}
html,body{width:1200px;height:3260px;overflow:hidden}
body{font-family:'Lato',Arial,sans-serif;color:var(--ink);background:var(--white);position:relative}
a{color:inherit;text-decoration:none}

/* hero */
.hero{position:absolute;left:0;top:0;width:1200px;height:780px;overflow:hidden}
.hero-photo{position:absolute;inset:0;background:
  radial-gradient(ellipse at 30% 70%,rgba(236,228,214,.55),transparent 55%),
  linear-gradient(160deg,#4a3a2c 0%,#6d5640 35%,#8d7a66 55%,#3b2f26 100%)}
.hero-shade{position:absolute;inset:0;background:linear-gradient(180deg,rgba(0,0,0,.45) 0%,rgba(0,0,0,.15) 40%,rgba(0,0,0,.25) 100%)}
.hero-curve{position:absolute;left:0;bottom:0;width:1200px;height:160px}
.top-bar{position:absolute;top:18px;right:120px;display:flex;gap:10px}
.top-bar span{font-size:13px;font-weight:700;color:var(--white);border:1px solid rgba(255,255,255,.8);padding:6px 14px;letter-spacing:.5px}
.site-header{position:absolute;top:40px;left:120px;width:960px;height:60px;display:flex;align-items:center;justify-content:space-between}
.brand{display:flex;align-items:center;gap:12px;font-size:40px;font-weight:900;color:var(--white);letter-spacing:2px}
.brand-dot{width:34px;height:34px;border-radius:50%;background:var(--white)}
.main-nav{display:flex;gap:28px;margin-top:24px}
.main-nav a{font-size:15px;font-weight:700;color:var(--white);letter-spacing:.5px}
.hero-copy{position:absolute;top:330px;left:0;width:1200px;text-align:center;color:var(--white)}
.hero-copy h1{font-size:62px;font-weight:900;line-height:1.08;letter-spacing:2px;text-shadow:0 2px 8px rgba(0,0,0,.35)}
.hero-copy p{font-size:24px;font-weight:700;line-height:1.3;margin-top:10px;letter-spacing:1px}
.slider-dots{position:absolute;top:644px;left:0;width:1200px;display:flex;justify-content:center;gap:10px}
.slider-dots i{width:12px;height:12px;border-radius:50%;background:rgba(255,255,255,.55)}
.slider-dots i.active{background:var(--white)}

/* features */
.features{position:absolute;top:775px;left:120px;width:960px;display:flex;justify-content:space-between}
.feature{width:300px;display:flex;gap:16px}
.feature-icon{flex:none;width:84px;height:84px;border-radius:50%;background:var(--brand);display:flex;align-items:center;justify-content:center;box-shadow:0 0 0 5px #dbe6f1}
.feature h3{font-size:22px;font-weight:900;margin-top:6px}
.feature p{font-size:12px;color:var(--muted);line-height:1.4;margin-top:6px;width:180px}
.feature .more{font-size:14px;font-weight:700;color:var(--brand);margin-top:10px;display:block}

/* speciality services */
.speciality{position:absolute;top:940px;left:0;width:1200px;height:720px;background:var(--grey-band)}
.speciality-curve{position:absolute;top:0;left:0;width:1200px;height:120px}
.section-mark{position:absolute;top:40px;left:580px;width:40px;height:40px;border-radius:50%;background:var(--ink)}
.section-title{font-size:34px;font-weight:900;text-align:center;letter-spacing:1px}
.speciality .section-title{position:absolute;top:118px;width:1200px}
.speciality .lead{position:absolute;top:172px;left:320px;width:560px;text-align:center;font-size:15px;line-height:1.45;color:var(--muted)}
.cards{position:absolute;top:292px;left:120px;width:960px;display:flex;justify-content:space-between}
.card{width:304px;height:342px;background:var(--white);box-shadow:0 3px 10px rgba(0,0,0,.12);position:relative;text-align:center}
.card-photo{height:188px}
.card h4{font-size:21px;font-weight:900;line-height:1.15;margin-top:14px}
.card p{font-size:12px;color:var(--muted);line-height:1.4;margin:8px 40px 0}
.btn{display:inline-block;background:var(--brand);color:var(--white);font-size:14px;font-weight:700;letter-spacing:.5px;padding:11px 24px}
.card .btn{position:absolute;bottom:-20px;left:50%;transform:translateX(-50%)}
.photo-kitchen{background:linear-gradient(135deg,#5b4a3d,#a98d70 50%,#3c3a3a)}
.photo-dining{background:linear-gradient(135deg,#2e2620,#8a5f3c 50%,#d7b58b)}
.photo-lamp{background:linear-gradient(135deg,#33363a,#6b6f74 50%,#c8a46c)}

/* about */
.about{position:absolute;top:1740px;left:0;width:1200px;height:510px;overflow:hidden}
.about-photo{position:absolute;top:0;left:500px;width:700px;height:510px;background:linear-gradient(120deg,#d9d5cf 0%,#b9a48d 40%,#8c6a4f 70%,#c7bcb0 100%)}
.about-panel{position:absolute;top:0;left:0;width:720px;height:510px}
.about-copy{position:absolute;top:110px;left:120px;width:420px;color:var(--white)}
.about-copy h2{font-size:42px;font-weight:900;letter-spacing:1px}
.about-copy p{font-size:15px;line-height:1.45;margin-top:14px;opacity:.92}
.btn-outline{display:inline-block;margin-top:28px;border:2px solid var(--white);color:var(--white);font-size:14px;font-weight:700;padding:12px 26px;letter-spacing:.5px}

/* news */
.news{position:absolute;top:2280px;left:120px;width:960px}
.news h2{font-size:30px;font-weight:900;color:var(--brand);letter-spacing:.5px}
.news-list{display:flex;justify-content:space-between;margin-top:32px}
.news-card{width:304px;height:400px;background:var(--white);box-shadow:0 3px 10px rgba(0,0,0,.12);position:relative}
.news-photo{height:178px}
.news-card h4{font-size:18px;font-weight:900;color:var(--brand);line-height:1.2;margin:20px 22px 0}
.news-card p{font-size:12px;color:var(--muted);line-height:1.4;margin:10px 22px 0}
.news-card .btn{position:absolute;left:22px;bottom:26px;font-size:12px;padding:8px 16px}
.photo-wood{background:linear-gradient(135deg,#8b6a44,#c99c62 50%,#5e4530)}
.photo-table{background:linear-gradient(135deg,#3e4a2f,#7d8a5a 45%,#c9bfa6)}
.photo-living{background:linear-gradient(135deg,#b9bcc0,#e8e6e1 50%,#7d7f84)}

/* footer */
.site-footer{position:absolute;top:2850px;left:0;width:1200px;height:340px;background:var(--footer-bg)}
.footer-inner{position:absolute;top:66px;left:120px;width:960px;display:flex}
.footer-brand{width:240px;display:flex;align-items:center;gap:10px;font-size:40px;font-weight:900;color:var(--ink);letter-spacing:2px;height:60px}
.footer-brand .brand-dot{background:var(--ink);width:30px;height:30px}
.footer-col h5{font-size:15px;font-weight:900;margin-bottom:14px;letter-spacing:.5px}
.footer-col li{list-style:none;font-size:13px;color:var(--ink);line-height:1.75;display:flex;align-items:center;gap:10px}
.col-contact{width:300px}
.col-contact li{align-items:flex-start;line-height:1.35;margin-bottom:12px}
.col-company{width:220px}
.col-social li{margin-bottom:6px}
.social-dot{width:24px;height:24px;border-radius:50%;background:var(--brand);flex:none}
.copyright{position:absolute;top:3190px;left:0;width:1200px;height:70px;text-align:center;font-size:12px;color:var(--muted);padding-top:18px}
</style>
</head>
<body>

<section class="hero">
  <div class="hero-photo" role="img" aria-label="Modern bathroom with dark wooden vanity, basin and bathtub"></div>
  <div class="hero-shade"></div>
  <svg class="hero-curve" viewBox="0 0 1200 160" preserveAspectRatio="none" aria-hidden="true">
    <path d="M0 60 C300 150 700 150 1200 40 L1200 160 L0 160 Z" fill="#ffffff"/>
  </svg>
  <div class="top-bar"><span>ENGLISH ▾</span><span>LOG IN</span></div>
  <header class="site-header">
    <div class="brand"><span class="brand-dot"></span>VELK</div>
    <nav class="main-nav">
      <a href="#">ABOUT</a><a href="#">BRAND NEW</a><a href="#">CATALOG CONFIGURATOR</a><a href="#">LIGHT CONFIGURATOR</a><a href="#">LAMP</a>
    </nav>
  </header>
  <div class="hero-copy">
    <h1>DECORATIVE<br>FURNITURE FITTINGS</h1>
    <p>FUNCTIONALITY MEETS DESIGN.<br>BE INSPIRED BY THE VELK COLLECTION</p>
  </div>
  <div class="slider-dots"><i class="active"></i><i></i><i></i><i></i></div>
</section>

<section class="features">
  <div class="feature">
    <div class="feature-icon"><svg width="40" height="40" viewBox="0 0 40 40" aria-hidden="true"><path d="M20 4l4.7 10 10.8 1.2-8 7.3 2.3 10.7L20 27.8 10.2 33.2l2.3-10.7-8-7.3L15.3 14z" fill="none" stroke="#fff" stroke-width="2.5" stroke-linejoin="round"/></svg></div>
    <div><h3>BEST DESIGNS</h3><p>Sturdy hinges and runners made to last through years of daily use at home.</p><a class="more" href="#">Click here ›</a></div>
  </div>
  <div class="feature">
    <div class="feature-icon"><svg width="40" height="40" viewBox="0 0 40 40" aria-hidden="true"><circle cx="20" cy="16" r="10" fill="none" stroke="#fff" stroke-width="2.5"/><path d="M13 24l-3 12 10-5 10 5-3-12" fill="none" stroke="#fff" stroke-width="2.5" stroke-linejoin="round"/></svg></div>
    <div><h3>TOP QUALITY</h3><p>Every fitting is tested for load, motion and finish before it leaves our plant.</p><a class="more" href="#">Click here ›</a></div>
  </div>
  <div class="feature">
    <div class="feature-icon"><svg width="40" height="40" viewBox="0 0 40 40" aria-hidden="true"><path d="M20 4l14 8v16l-14 8-14-8V12z M6 12l14 8 14-8 M20 20v16" fill="none" stroke="#fff" stroke-width="2.5" stroke-linejoin="round"/></svg></div>
    <div><h3>TOP FURNITURE</h3><p>Handles, lifts and drawer systems chosen by cabinet makers across the whole country.</p><a class="more" href="#">Click here ›</a></div>
  </div>
</section>

<section class="speciality">
  <svg class="speciality-curve" viewBox="0 0 1200 120" preserveAspectRatio="none" aria-hidden="true">
    <path d="M0 0 L1200 0 L1200 20 C800 110 400 110 0 30 Z" fill="#ffffff"/>
  </svg>
  <span class="section-mark"></span>
  <h2 class="section-title">SPECIALITY SERVICES</h2>
  <p class="lead">Aliamcorper est eget bibendum cursus neque mi consectetuer mi a ultricies massa est sed nisl Class aptent taciti sociosqu ad litora torquent per conubia nostra</p>
  <div class="cards">
    <article class="card">
      <div class="card-photo photo-kitchen" role="img" aria-label="Modern kitchen with wooden cabinets"></div>
      <h4>CATALOG<br>CONFIGURATOR</h4>
      <p>Pick fronts, fittings and finishes and see your cabinet take shape step by step.</p>
      <a class="btn" href="#">READ MORE</a>
    </article>
    <article class="card">
      <div class="card-photo photo-dining" role="img" aria-label="Dining room with pendant lights above a wooden table"></div>
      <h4>LIGHT<br>CONFIGURATOR</h4>
      <p>Plan lighting for shelves, drawers and wardrobes with matching drivers and switches included.</p>
      <a class="btn" href="#">READ MORE</a>
    </article>
    <article class="card">
      <div class="card-photo photo-lamp" role="img" aria-label="Warm pendant lamps in a dark interior"></div>
      <h4>LAMP</h4>
      <p>Compact lamps for kitchens and living rooms in warm or cool white tones.</p>
      <a class="btn" href="#">READ MORE</a>
    </article>
  </div>
</section>

<section class="about">
  <div class="about-photo" role="img" aria-label="Showroom wall displaying furniture handles and finish samples"></div>
  <svg class="about-panel" viewBox="0 0 720 510" preserveAspectRatio="none" aria-hidden="true">
    <polygon points="0,0 720,0 600,510 0,510" fill="#3176b5"/>
  </svg>
  <div class="about-copy">
    <h2>ABOUT VELK</h2>
    <p>Praesent elementum elit at tellus nec ultricies du amet porttitor mattis enim in felis mauris ipsum Nunc interdum nisl blandit sed nulla in ullamcorper est</p>
    <p>eget semper cursus neque mi consectetuer mi a ultricies massa est sed nisl Class</p>
    <a class="btn-outline" href="#">READ MORE</a>
  </div>
</section>

<section class="news">
  <h2>NEWS &amp; BLOGS</h2>
  <div class="news-list">
    <article class="news-card">
      <div class="news-photo photo-wood" role="img" aria-label="Open wooden drawer with fittings"></div>
      <h4>Pellentesque faucibus Ut accumsan ultricies Maecenas</h4>
      <p>A short look at how soft close runners changed the modern kitchen drawer for good.</p>
      <a class="btn" href="#">READ MORE</a>
    </article>
    <article class="news-card">
      <div class="news-photo photo-table" role="img" aria-label="Wooden dining table with chairs beside a window"></div>
      <h4>Mauris vel lacus vitae felis venenatis volutpat Etiam non nunc</h4>
      <p>Our team visited a workshop that builds custom dining tables from reclaimed oak boards.</p>
      <a class="btn" href="#">READ MORE</a>
    </article>
    <article class="news-card">
      <div class="news-photo photo-living" role="img" aria-label="Bright living room with sofa and shelving"></div>
      <h4>Fusce ultricies orci ac feugiat suscipit leo Nullam</h4>
      <p>Five simple ideas for bright, tidy living rooms using hidden storage and clever lighting.</p>
      <a class="btn" href="#">READ MORE</a>
    </article>
  </div>
</section>

<footer class="site-footer">
  <div class="footer-inner">
    <div class="footer-brand"><span class="brand-dot"></span>VELK</div>
    <div class="footer-col col-contact">
      <h5>CONTACT US</h5>
      <ul>
        <li><svg width="16" height="18" viewBox="0 0 16 18" aria-hidden="true"><path d="M8 1a6 6 0 0 0-6 6c0 4.5 6 10 6 10s6-5.5 6-10a6 6 0 0 0-6-6z" fill="#3176b5"/><circle cx="8" cy="7" r="2.2" fill="#fff"/></svg><span>4410 ORCHARD LANE SUITE 12<br>DALLAS 75201 TX</span></li>
        <li><svg width="16" height="16" viewBox="0 0 16 16" aria-hidden="true"><path d="M3 1h3l1.5 4-2 1.3a9 9 0 0 0 4.2 4.2L11 8.5l4 1.5v3a2 2 0 0 1-2 2A12 12 0 0 1 1 3a2 2 0 0 1 2-2z" fill="#3176b5"/></svg><span>555-014-2287</span></li>
        <li><svg width="16" height="14" viewBox="0 0 16 14" aria-hidden="true"><rect x="1" y="2" width="14" height="10" fill="#3176b5"/><path d="M1 2l7 6 7-6" fill="none" stroke="#fff" stroke-width="1.4"/></svg><span>INFO@VELK-EXAMPLE.AT</span></li>
      </ul>
    </div>
    <div class="footer-col col-company">
      <h5>COMPANY</h5>
      <ul><li>ABOUT</li><li>BRAND NEW</li><li>CATALOG CONFIGURATOR</li><li>LIGHT CONFIGURATOR</li><li>LAMP</li><li>CONTACT</li></ul>
    </div>
    <div class="footer-col col-social">
      <h5>GET IN TOUCH</h5>
      <ul>
        <li><span class="social-dot"></span>CHIRPLINE</li>
        <li><span class="social-dot"></span>FRIENDWALL</li>
        <li><span class="social-dot"></span>WORKLINK</li>
        <li><span class="social-dot"></span>SNAPGRID</li>
      </ul>
    </div>
  </div>
</footer>
<p class="copyright">Copyright © 2024 All rights reserved</p>

</body>
</html>
```